QuillVane needs a dashboard page designed

Redesign the dashboard shown in the provided images.

There are two images:
- dashboard.png
- dashboard-expanded.png

NOTE: The vocabulary navigation on the left will be a very long list of words 100s, so keep that in mind when you're designing both the vocab navigation and the expanded vocab popup.

In the dashboard.png picture, there needs to be a progress chart showing the word progress like the following: review 1(show it as completed) -> review 2(show the user they are here) -> review 3(unvisited) -> review 4(unvisited)

The do-not-design-this-page.png image is for your reference only. It is not to be designed. Use it to understand the overall look and feel of the website to help you create the best dashboard page possible.
Updates

Need extra days to review

Industry/Entity Type

Education English learning

Number of Pages Required

1 page

Requirements
Must have
• The main navigation and main header cannot change between pages. See the do-not-design page for the main navigateion and header.
Should not have
• Do not add a person profile. We will not have images of our users. Keep the icons in the main navigation as they are.

```html
<!DOCTYPE html>
<html lang="en">
<head>
<meta charset="utf-8">
<title>QuillVane Dashboard</title>
<link href="https://fonts.googleapis.com/css2?family=Poppins:wght@400;500;600;700&display=swap" rel="stylesheet">
<style>
:root{
  --ink:#1b1029;
  --rail:#1d1129;
  --panel:#2b1d38;
  --panel-line:#4a3a58;
  --muted:#c9bfd4;
  --white:#ffffff;
  --purple:#6b5bd2;
  --purple-bg:#f1eeff;
  --orange:#e8763f;
  --orange-bg:#fff2ea;
  --cyan:#1a9ec2;
  --cyan-bg:#ebf8fc;
  --yellow:#f2b428;
  --yellow-bg:#fff2d2;
  --green:#7cb342;
  --text:#1b1b1f;
  --card-line:#e4e0ea;
  --band-long:#f2f0fd;
  --band-work:#edf9ef;
  --band-short:#fff3ec;
  --band-forgot:#edf8fc;
}
*{box-sizing:border-box;margin:0;padding:0}
html,body{width:1200px;height:844px;overflow:hidden}
body{font-family:"Poppins",sans-serif;background:var(--white);color:var(--text);position:relative}
.topbar{position:absolute;left:0;top:0;width:1200px;height:44px;background:var(--ink);color:var(--white);display:flex;align-items:center;padding:0 18px}
.brand{font-weight:700;font-size:16px;display:flex;align-items:center;gap:6px}
.top-actions{margin-left:auto;display:flex;align-items:center;gap:10px}
.avatar{width:30px;height:30px;border-radius:50%;background:var(--yellow);color:var(--white);font-weight:700;font-size:16px;display:flex;align-items:center;justify-content:center;margin-left:4px}
.rail{position:absolute;left:0;top:44px;width:52px;height:800px;background:var(--rail);color:var(--white)}
.rail-item{display:flex;flex-direction:column;align-items:center;font-size:8px;line-height:9px;text-align:center;margin-top:10px;gap:3px}
.rail-item.active{color:var(--yellow);font-weight:600}
.vocab{position:absolute;left:52px;top:44px;width:198px;height:800px;background:linear-gradient(180deg,#3a2b47 0%,var(--panel) 30%,var(--rail) 100%);border-top-left-radius:22px;color:var(--white);padding:0 0 0 24px}
.vocab-filter{display:flex;align-items:center;justify-content:space-between;height:59px;padding-right:20px;border-bottom:1px solid var(--panel-line);margin-right:20px;font-size:12px;font-weight:500}
.expand{position:absolute;right:-14px;top:28px;width:26px;height:26px;border-radius:50%;background:var(--white);display:flex;align-items:center;justify-content:center}
.group{position:relative;margin-top:18px}
.group h3{font-size:13px;font-weight:600;line-height:16px}
.help{position:absolute;right:20px;top:1px;width:14px;height:14px;border:1.3px solid var(--white);border-radius:50%;font-size:9px;display:flex;align-items:center;justify-content:center}
.current-word{font-size:11px;font-weight:700;color:var(--green);letter-spacing:.5px}
.word-list{list-style:none;margin-top:5px}
.word-list li{font-size:11.5px;color:var(--muted);line-height:17.8px}
.give{font-size:11.5px;color:var(--white)}
.steps{position:absolute;left:274px;top:71px;display:flex;gap:6px}
.step{width:221px;height:82px;border-radius:7px;border:1px solid;position:relative;padding:18px 0 0 31px}
.step-label{font-size:11px;line-height:14px}
.step-state{font-size:12px;font-weight:600;margin-top:4px}
.step-bar{position:absolute;left:31px;top:61px;width:118px;height:3px;border-radius:2px;background:var(--white)}
.step-bar span{display:block;height:100%;border-radius:2px}
.step-dot{position:absolute;left:157px;top:20px;width:42px;height:42px;border-radius:50%;background:var(--white);display:flex;align-items:center;justify-content:center}
.s1{background:var(--purple-bg);border-color:var(--purple)}.s1 .step-state{color:var(--purple)}
.s2{background:var(--orange-bg);border-color:var(--orange)}.s2 .step-state{color:var(--orange)}
.s3{background:var(--cyan-bg);border-color:var(--cyan)}.s3 .step-state{color:var(--cyan)}
.s4{background:var(--yellow-bg);border-color:var(--yellow)}.s4 .step-state{color:var(--yellow)}
.word-card{position:absolute;left:274px;top:194px;width:675px;height:138px;border:1px solid var(--card-line);border-radius:7px;padding:20px 27px 0}
.word-card h1{font-size:20px;font-weight:600;display:flex;align-items:center;gap:8px;line-height:24px}
.word-card p{font-size:11.4px;line-height:16px;margin-top:2px}
.exercise{position:absolute;left:956px;top:194px;width:220px;height:137px;background:var(--yellow-bg);border-radius:7px;text-align:center}
.exercise-art{position:absolute;left:55px;top:-28px;width:115px;height:104px;border-radius:40px 40px 10px 10px;background:radial-gradient(circle at 50% 45%,#f6c64a 0%,#f3d27c 55%,rgba(255,242,210,0) 75%)}
.exercise span{position:absolute;left:0;right:0;top:91px;font-size:8.8px;font-weight:700;line-height:12px}
.graph-card{position:absolute;left:275px;top:342px;width:899px;height:483px;border:1px solid var(--card-line);border-radius:7px;box-shadow:0 4px 18px rgba(40,20,60,.06)}
.graph-card h2{position:absolute;left:31px;top:27px;font-size:20px;font-weight:600}
.graph-card svg{position:absolute;left:0;top:0}
.analysis{position:absolute;left:31px;top:366px;width:840px}
.analysis h2{position:static;font-size:21px}
.analysis p{font-size:11.2px;line-height:16px;margin-top:6px}
</style>
</head>
<body>
<header class="topbar">
  <div class="brand">QuillVane <svg width="12" height="8" viewBox="0 0 12 8"><path d="M1 1l5 5 5-5" stroke="#fff" stroke-width="2" fill="none"/></svg></div>
  <div class="top-actions">
    <svg width="16" height="16" viewBox="0 0 16 16"><circle cx="8" cy="8" r="6.5" stroke="#fff" stroke-width="1.4" fill="none"/><path d="M5 8l2 2 4-4" stroke="#fff" stroke-width="1.4" fill="none"/></svg>
    <svg width="17" height="17" viewBox="0 0 16 16"><circle cx="8" cy="8" r="2.5" stroke="#fff" stroke-width="1.4" fill="none"/><circle cx="8" cy="8" r="6" stroke="#fff" stroke-width="1.4" stroke-dasharray="3 1.7" fill="none"/></svg>
    <svg width="16" height="16" viewBox="0 0 16 16"><path d="M3 12h10l-1.5-2V7a3.5 3.5 0 0 0-7 0v3z M6.5 13.5a1.5 1.5 0 0 0 3 0" stroke="#fff" stroke-width="1.4" fill="none"/></svg>
    <div class="avatar">S</div>
    <svg width="10" height="7" viewBox="0 0 12 8"><path d="M1 1l5 5 5-5" stroke="#fff" stroke-width="2" fill="none"/></svg>
  </div>
</header>

<nav class="rail">
  <div class="rail-item active"><svg width="14" height="14" viewBox="0 0 14 14"><path d="M1 7L7 1l6 6v6H9V9H5v4H1z" fill="#f2b428"/></svg>QuillVane</div>
  <div class="rail-item" style="margin-top:14px"><svg width="14" height="17" viewBox="0 0 14 17"><path d="M7 0a6 6 0 0 0-6 6c0 4 6 11 6 11s6-7 6-11a6 6 0 0 0-6-6z" fill="#fff"/><circle cx="7" cy="6" r="2.2" fill="#1d1129"/></svg>Daily<br>English</div>
  <div class="rail-item" style="margin-top:20px"><svg width="14" height="16" viewBox="0 0 14 16"><rect x="1" y="1" width="12" height="15" fill="#fff"/><g fill="#1d1129"><rect x="3" y="3" width="2" height="2"/><rect x="9" y="3" width="2" height="2"/><rect x="3" y="7" width="2" height="2"/><rect x="9" y="7" width="2" height="2"/><rect x="6" y="12" width="2" height="4"/></g></svg>Business</div>
</nav>

<aside class="vocab">
  <div class="vocab-filter">All <svg width="11" height="7" viewBox="0 0 12 8"><path d="M1 1l5 5 5-5" stroke="#fff" stroke-width="2" fill="none"/></svg></div>
  <div class="expand"><svg width="13" height="13" viewBox="0 0 14 14"><path d="M6 2H2v10h10V8M8 2h4v4M12 2L6 8" stroke="#1d1129" stroke-width="1.6" fill="none"/></svg></div>
  <div class="group">
    <h3>Short-Term Memory</h3><div class="help">?</div>
    <div class="current-word">GRAB</div>
  </div>
  <div class="group">
    <h3>Working Memory</h3><div class="help">?</div>
    <ul class="word-list">
      <li>Cool Down</li><li>Crav</li><li>Go For</li><li>Go-To</li><li>In The Mood For</li><li>Slp</li><li>Soothing</li><li>Stick With</li><li>Throw In/Throw On</li>
    </ul>
  </div>
  <div class="group">
    <h3>Long-Term Memory</h3><div class="help">?</div>
    <div class="give">Give ItA Try</div>
  </div>
</aside>

<section class="steps">
  <div class="step s1"><div class="step-label">REVIEW 1</div><div class="step-state">Completed</div><div class="step-bar"><span style="width:100%;background:var(--purple)"></span></div><div class="step-dot"><svg width="20" height="20" viewBox="0 0 20 20"><circle cx="10" cy="10" r="9" fill="#6b5bd2"/><path d="M6 10l3 3 5-6" stroke="#fff" stroke-width="2" fill="none"/></svg></div></div>
  <div class="step s2"><div class="step-label">REVIEW 2</div><div class="step-state">You are here</div><div class="step-bar"><span style="width:40%;background:var(--orange)"></span></div><div class="step-dot"><svg width="14" height="16" viewBox="0 0 14 16"><circle cx="7" cy="4" r="3.2" fill="#e8763f"/><path d="M1 15a6 6 0 0 1 12 0z" fill="#e8763f"/></svg></div></div>
  <div class="step s3"><div class="step-label">REVIEW 3</div><div class="step-state">Unvisited</div><div class="step-bar"></div><div class="step-dot"></div></div>
  <div class="step s4"><div class="step-label">REVIEW 4</div><div class="step-state">Unvisited</div><div class="step-bar"></div><div class="step-dot"></div></div>
</section>

<article class="word-card">
  <h1>Grab <svg width="20" height="19" viewBox="0 0 24 23"><path d="M12 1l3.3 7 7.7.9-5.7 5.2 1.6 7.6L12 17.9 5.1 21.7l1.6-7.6L1 8.9 8.7 8z" fill="#f2b428"/></svg></h1>
  <p>The word <b>"grab"</b> is most commonly used as a <b>verb,</b> meaning <b>to take something quickly or suddenly</b>. Imagine you're running late for school. You don't have time for breakfast, so you quickly <b>grab</b> an apple from the kitchen and rush out the door. As you reach the bus stop, your friend waves &amp; says, "Hey! Let's <b>grab</b> a coffee after class." Later, when you sit down, your phone starts ringing. You <b>grab</b> it from your bag and answer.</p>
</article>

<div class="exercise">
  <div class="exercise-art" role="img" aria-label="Illustration of a student reading a book surrounded by study icons"></div>
  <span>START VOCABULARY<br>REVIEW EXERCISE 3</span>
</div>

<section class="graph-card">
  <h2>Learning Curve Graph</h2>
  <svg width="899" height="360" viewBox="0 0 899 360" font-family="Poppins, sans-serif">
    <defs>
      <linearGradient id="fadeL" x1="0" x2="1"><stop offset="0" stop-color="#f2f0fd"/><stop offset="1" stop-color="#f2f0fd" stop-opacity="0"/></linearGradient>
      <linearGradient id="fadeW" x1="0" x2="1"><stop offset="0" stop-color="#edf9ef"/><stop offset=".75" stop-color="#edf9ef"/><stop offset="1" stop-color="#edf9ef" stop-opacity="0"/></linearGradient>
      <linearGradient id="fadeS" x1="0" x2="1"><stop offset="0" stop-color="#fff3ec"/><stop offset=".8" stop-color="#fff3ec"/><stop offset="1" stop-color="#fff3ec" stop-opacity="0"/></linearGradient>
      <linearGradient id="fadeF" x1="0" x2="1"><stop offset="0" stop-color="#edf8fc"/><stop offset=".8" stop-color="#edf8fc"/><stop offset="1" stop-color="#edf8fc" stop-opacity="0"/></linearGradient>
    </defs>
    <rect x="30" y="62" width="775" height="50" fill="url(#fadeL)"/>
    <rect x="30" y="112" width="775" height="109" fill="url(#fadeW)"/>
    <rect x="30" y="221" width="775" height="35" fill="url(#fadeS)"/>
    <rect x="30" y="256" width="775" height="35" fill="url(#fadeF)"/>
    <g font-size="10" fill="#555">
      <text x="44" y="90">Long-term Memory</text>
      <text x="44" y="170">Working Memory</text>
      <text x="44" y="242">Short-Term Memory</text>
      <text x="44" y="277">Forgotten Memory</text>
    </g>
    <line x1="30" y1="291" x2="858" y2="291" stroke="#ddd"/>
    <line x1="19" y1="297" x2="19" y2="310" stroke="#ccc"/>
    <line x1="890" y1="297" x2="890" y2="310" stroke="#ccc"/>
    <g stroke="#ccc">
      <line x1="94" y1="292" x2="94" y2="300"/><line x1="141" y1="292" x2="141" y2="300"/><line x1="188" y1="292" x2="188" y2="300"/><line x1="235" y1="292" x2="235" y2="300"/><line x1="282" y1="292" x2="282" y2="300"/><line x1="330" y1="292" x2="330" y2="300"/><line x1="377" y1="292" x2="377" y2="300"/><line x1="424" y1="292" x2="424" y2="300"/><line x1="472" y1="292" x2="472" y2="300"/><line x1="519" y1="292" x2="519" y2="300"/><line x1="566" y1="292" x2="566" y2="300"/><line x1="613" y1="292" x2="613" y2="300"/><line x1="661" y1="292" x2="661" y2="300"/><line x1="708" y1="292" x2="708" y2="300"/><line x1="756" y1="292" x2="756" y2="300"/>
    </g>
    <g font-size="8.5" fill="#222" text-anchor="middle">
      <text x="46" y="324">18 May</text><text x="96" y="324">12:00</text><text x="143" y="324">19 May</text><text x="192" y="324">12:00</text><text x="240" y="324">20 May</text><text x="290" y="324">12:00</text><text x="338" y="324">21 May</text><text x="387" y="324">12:00</text><text x="435" y="324">22 May</text><text x="484" y="324">12:00</text><text x="533" y="324">23 May</text><text x="582" y="324">12:00</text><text x="630" y="324">24 May</text><text x="679" y="324">12:00</text><text x="728" y="324">25 May</text><text x="777" y="324">12:00</text><text x="825" y="324">26 May</text>
    </g>
    <text x="460" y="351" font-size="10" font-weight="500" text-anchor="middle" fill="#222">DATE RANGE</text>
    <path d="M334 240 C380 240 415 268 422 291" stroke="#777" stroke-width="1.2" stroke-dasharray="1.5 3" fill="none"/>
    <path d="M430 137 C520 137 613 200 613 291" stroke="#777" stroke-width="1.2" stroke-dasharray="1.5 3" fill="none"/>
    <line x1="330" y1="242" x2="330" y2="291" stroke="#1b1029" stroke-width="8" stroke-linecap="round"/>
    <line x1="426" y1="139" x2="426" y2="291" stroke="#1b1029" stroke-width="8" stroke-linecap="round"/>
    <rect x="307" y="213" width="46" height="19" rx="4" fill="#fff" stroke="#eee"/>
    <text x="330" y="226" font-size="8.5" text-anchor="middle">21 May</text>
    <rect x="403" y="101" width="46" height="19" rx="4" fill="#fff" stroke="#eee"/>
    <text x="426" y="114" font-size="8.5" text-anchor="middle">22 May</text>
  </svg>
  <div class="analysis">
    <h2>QuillVane Learning Analysis</h2>
    <p>Lorem ipsum <b>dolor</b> sit amet, consectetur adipiscing elit. Nam <b>rutrum commodo</b> enim id bibendum. Nunc dignissim risus <b>dolor</b>nec finibus dictum eu. Aliquam sit amet euismod metus, quis malesuada erat. Sed at felis quis nulla feugiat cursus at at <b>dolor</b>. Maecenas pretium alquet dapibus. Fusce et eleifend massa.&nbsp; Sed convallis ex mi, at lobortis ligula congue vel.</p>
  </div>
</section>
</body>
</html>
```